Creative, fresh business card design for Ripplecraft Facades

We need a fresh, creative business card design for Ripplecraft Facades. We are the manufacturer of Ripplecraft Facades in Australia. Wall panels are 2400 x 1200mm panels made from MDF and feature 3D patterns on the face of the panel. The colours to be used are green, silver/grey and white RGB
Red 187
Green 207
Blue 65.

An idea is to possibly use a watermark of one of our designs as a background (like on the "Grids" design on the left hand side of page 2 of our brochure).

Target Market(s)

Interior designers, architects, builders and home renovators

Industry/Entity Type

Business

Contact Information for Business Card

Details to go on the card are:
Our logo (attached),
Slogan: "Decorative panels for interiors and exteriors",
Contact name,
Position,
Mobile phone number,
Business address,
Business phone,
Business fax,
Website and
Email address.

I have attached a few images of our panels and our brochure for reference.

The colours of the business card should feature our logo colours which are: RGB
Red 187
Green 207
Blue 65

Requirements
Must have
• Very modern fonts and design. Some of the designs shown especially the "Prisms" design which is a popular design.
Nice to have
• Creative but simple design. Very contemporary.
Should not have
• Anything ornate or old fashioned.

```html
<!DOCTYPE html>
<html lang="en">
<head>
<meta charset="utf-8">
<title>Ripplecraft Facades – Business Card</title>
<link rel="stylesheet" href="https://fonts.googleapis.com/css2?family=Open+Sans:wght@300;400;600;700&family=Arimo:wght@700&display=swap">
<style>
  :root {
    --backdrop: #2a2a2a;
    --card: #141414;
    --card-edge: #1e1e1e;
    --lime: #bbcf41;
    --silver: #a3a3a3;
    --white: #e9e9e9;
    --divider: #8a8a8a;
  }
  * { box-sizing: border-box; margin: 0; padding: 0; }
  html, body {
    width: 1200px; height: 1000px; overflow: hidden;
    background: var(--backdrop);
  }
  .canvas {
    position: relative; width: 1200px; height: 1000px;
  }
  .card {
    position: absolute; left: 232px; top: 290px;
    width: 736px; height: 420px;
    border-radius: 26px;
    background: linear-gradient(135deg, var(--card-edge) 0%, var(--card) 60%, #0f0f0f 100%);
    box-shadow: 0 20px 50px rgba(0,0,0,.45);
    font-family: "Open Sans", Arial, sans-serif;
    color: var(--white);
  }
  .brand {
    position: absolute; left: 120px; top: 150px; width: 240px;
  }
  .brand-mark {
    display: flex; align-items: center; gap: 12px;
  }
  .brand-square {
    width: 46px; height: 46px; background: var(--lime); flex: none;
  }
  .brand-name {
    font-family: "Open Sans", Arial, sans-serif;
    font-weight: 600; font-size: 21px; line-height: 1.15;
    color: var(--lime);
  }
  .brand-slogan {
    margin-top: 14px;
    font-weight: 300; font-size: 13px; letter-spacing: 1.6px; line-height: 1.35;
    color: var(--silver);
  }
  .divider {
    position: absolute; left: 384px; top: 100px;
    width: 1px; height: 220px; background: var(--divider);
  }
  .contact {
    position: absolute; left: 408px; top: 104px;
  }
  .contact-name {
    font-family: "Arimo", Arial, sans-serif;
    font-weight: 700; font-size: 22px; color: var(--lime);
  }
  .contact-role { font-size: 13px; color: var(--white); margin-top: 2px; }
  .contact-address {
    margin-top: 14px; font-size: 13px; font-weight: 600; line-height: 1.4;
  }
  .contact-lines { margin-top: 14px; list-style: none; }
  .contact-lines li {
    display: flex; align-items: center; gap: 12px;
    font-size: 13.5px; line-height: 22px; font-weight: 400;
  }
  .contact-lines svg { width: 13px; height: 13px; flex: none; fill: var(--lime); }
  .web-accent { color: var(--lime); }
</style>
</head>
<body>
<div class="canvas">
  <div class="card">
    <div class="brand">
      <div class="brand-mark">
        <span class="brand-square"></span>
        <span class="brand-name">Ripplecraft Facades</span>
      </div>
      <p class="brand-slogan">decorative panels for<br>interiors &amp; landscapes</p>
    </div>

    <div class="divider"></div>

    <div class="contact">
      <h1 class="contact-name">Nadia Carlow</h1>
      <p class="contact-role">Director</p>
      <p class="contact-address">14 Kestrel Lane,<br>Brookvale, 2100</p>
      <ul class="contact-lines">
        <li>
          <svg viewBox="0 0 16 16"><rect x="4" y="1" width="8" height="14" rx="1.5" fill="none" stroke="#bbcf41" stroke-width="1.6"/><circle cx="8" cy="12.5" r="1"/></svg>
          +000 123 456 789
        </li>
        <li>
          <svg viewBox="0 0 16 16"><path d="M3 1.5l3 .5 1 3.5-2 1.5c1 2 2.5 3.5 4.5 4.5l1.5-2 3.5 1 .5 3-2 1.5C7 14 2 9 1.5 3.5z"/></svg>
          +000 123 456 789
        </li>
        <li>
          <svg viewBox="0 0 16 16"><rect x="4" y="1" width="8" height="5"/><rect x="1" y="6" width="14" height="8" rx="1"/><rect x="4" y="10" width="8" height="1.5" fill="#141414"/></svg>
          +000 123 456 789
        </li>
        <li>
          <svg viewBox="0 0 16 16"><rect x="1" y="3" width="14" height="10" rx="1"/><path d="M1.5 3.5L8 9l6.5-5.5" fill="none" stroke="#141414" stroke-width="1.4"/></svg>
          nadia@ripplecraft.example
        </li>
        <li>
          <svg viewBox="0 0 16 16"><circle cx="9.5" cy="6.5" r="4.2" fill="none" stroke="#bbcf41" stroke-width="2"/><path d="M6.5 9.5L1.5 14.5" stroke="#bbcf41" stroke-width="2.4"/></svg>
          <span>www.<span class="web-accent">ripplecraft</span>.example</span>
        </li>
      </ul>
    </div>
  </div>
</div>
</body>
</html>
```